Clear Coat 5L & 2.5L kit

Clear coat 5 Liter with 2.5 Liter hardener
I attached few examples
Required size:
5L
Actual size is: 22.875 x 10.4375 inch
With bleed added: 23.125 x 10.6875 inch
2.5L
Actual size is: 22.875 x 6.1875 inch
With bleed added: 23.125x6.2125 inch

Thanks

```html
<!DOCTYPE html>
<html lang="en">
<head>
<meta charset="utf-8">
<title>Verano Autocoat – Ultra Clear Coat Kit</title>
<link href="https://fonts.googleapis.com/css2?family=Montserrat:wght@500;700;800&family=Roboto+Condensed:wght@400;700&display=swap" rel="stylesheet">
<style>
  :root {
    --ink: #1f2c2e;
    --green: #22d36b;
    --green-deep: #12b956;
    --green-light: #5ef59a;
    --silver-1: #ffffff;
    --silver-2: #d9dcdc;
    --silver-3: #a9adad;
    --side-dark: #aeb3b3;
    --side-light: #f1f2f2;
    --bg-top: #f6f8f8;
    --bg-bottom: #cfdde2;
  }
  html, body { margin: 0; padding: 0; overflow: hidden; }
  .canvas {
    position: relative;
    width: 1200px;
    height: 1199px;
    overflow: hidden;
    background: linear-gradient(180deg, var(--bg-top), var(--bg-bottom));
    font-family: "Montserrat", sans-serif;
    color: var(--ink);
  }
  .brand-mark {
    position: absolute;
    left: 742px;
    top: 96px;
    display: flex;
    align-items: center;
    gap: 14px;
  }
  .brand-mark .dot { width: 22px; height: 22px; background: var(--green); }
  .brand-name {
    margin: 0;
    font-weight: 800;
    color: var(--ink);
    line-height: .95;
    letter-spacing: -1px;
  }
  .brand-mark .brand-name { font-size: 76px; }
  .brand-name span { display: block; font-size: .62em; letter-spacing: 1px; }

  .label {
    position: absolute;
    overflow: hidden;
    background: linear-gradient(90deg, var(--silver-2), var(--silver-1) 35%, var(--silver-2) 80%, var(--silver-3));
  }
  .label svg.bands { position: absolute; inset: 0; width: 100%; height: 100%; }

  .label-side {
    background: linear-gradient(90deg, var(--side-dark), var(--side-light) 55%, #d3d6d6);
  }
  .label-side::after {
    content: "";
    position: absolute;
    inset: 0;
    background: linear-gradient(90deg, rgba(0,0,0,.18), rgba(0,0,0,0) 45%, rgba(0,0,0,.08));
    pointer-events: none;
  }
  .side-title {
    position: absolute;
    transform: rotate(-90deg);
    transform-origin: left top;
    font-size: 13px;
    font-weight: 500;
    letter-spacing: 1px;
    white-space: nowrap;
    z-index: 1;
  }
  .side-title b { font-weight: 800; }

  .label-large-side {
    left: 113px; top: 232px; width: 96px; height: 783px;
    clip-path: polygon(0 52px, 100% 0, 100% 100%, 0 calc(100% - 10px));
  }
  .label-large-front { left: 209px; top: 232px; width: 362px; height: 783px; }
  .label-small-side {
    left: 571px; top: 602px; width: 113px; height: 436px;
    clip-path: polygon(0 36px, 100% 0, 100% 100%, 0 calc(100% - 8px));
  }
  .label-small-front { left: 684px; top: 602px; width: 426px; height: 436px; }

  .content { position: absolute; inset: 0; }
  .content .brand-name { position: absolute; }
  .tag {
    display: inline-block;
    background: var(--ink);
    color: var(--green-light);
    font-family: "Roboto Condensed", sans-serif;
    font-weight: 400;
    padding: 0 6px;
    border-radius: 3px;
  }
  .product { margin: 0; font-weight: 700; line-height: 1; }
  .spec {
    font-family: "Roboto Condensed", sans-serif;
    font-weight: 700;
    line-height: 1.2;
  }
  .volume {
    position: absolute;
    font-family: "Roboto Condensed", sans-serif;
    font-weight: 700;
    color: #fff;
    line-height: 1;
  }
  .features {
    position: absolute;
    margin: 0; padding: 0; list-style: none;
    font-family: "Roboto Condensed", sans-serif;
    font-weight: 700;
    color: #f4fff7;
    font-size: 21px;
    line-height: 1.35;
  }
  .speed-badge {
    position: absolute;
    background: var(--ink);
    color: #fff;
    font-weight: 700;
    font-size: 26px;
    letter-spacing: 1px;
    padding: 10px 18px 16px;
    border-radius: 12px 12px 0 0;
  }
</style>
</head>
<body>
<main class="canvas">

  <div class="brand-mark">
    <p class="brand-name">VERANO<span>AUTOCOAT</span></p>
    <div class="dot"></div>
  </div>

  <!-- 5 L clear coat label -->
  <section class="label label-side label-large-side">
    <svg class="bands" viewBox="0 0 96 783" preserveAspectRatio="none" aria-hidden="true">
      <polygon points="0,470 96,420 96,783 0,783" fill="var(--green)"/>
      <polygon points="0,560 96,480 96,640 0,740" fill="var(--green-light)" opacity=".5"/>
      <polygon points="0,650 96,600 96,783 0,783" fill="var(--green-deep)" opacity=".35"/>
    </svg>
    <div class="side-title" style="left:38px; top:460px;">ULTRA <b>CLEAR COAT</b></div>
  </section>

  <section class="label label-large-front">
    <svg class="bands" viewBox="0 0 362 783" preserveAspectRatio="none" aria-hidden="true">
      <polygon points="0,430 362,520 362,783 0,783" fill="var(--green)"/>
      <polygon points="0,480 362,640 362,783 0,760" fill="var(--green-light)" opacity=".55"/>
      <polygon points="0,560 362,700 362,783 0,783" fill="var(--green-deep)" opacity=".5"/>
      <polygon points="180,410 362,560 362,580 170,420" fill="var(--green-deep)"/>
    </svg>
    <div class="content">
      <p class="brand-name" style="left:32px; top:58px; font-size:58px;">VERANO<span>AUTOCOAT</span></p>
      <div style="position:absolute; left:33px; top:290px;">
        <span class="tag" style="font-size:29px;">ULTRA</span>
        <h1 class="product" style="font-size:48px; margin-top:6px; letter-spacing:-1px;">CLEAR COAT</h1>
        <div class="spec" style="font-size:27px; margin-top:8px;">VOC 2.1<br>2:1 MIX</div>
      </div>
      <div class="volume" style="left:34px; top:672px; font-size:78px;">5L</div>
      <ul class="features" style="left:190px; top:650px;">
        <li>High Gloss</li>
        <li>Good Leveling</li>
        <li>Easy Application</li>
      </ul>
    </div>
  </section>

  <!-- 2.5 L hardener label -->
  <section class="label label-side label-small-side">
    <svg class="bands" viewBox="0 0 113 436" preserveAspectRatio="none" aria-hidden="true">
      <polygon points="0,250 113,160 113,436 0,436" fill="var(--green)"/>
      <polygon points="45,340 113,190 113,330" fill="var(--green-light)" opacity=".6"/>
    </svg>
    <div class="side-title" style="left:24px; top:290px;">ULTRA <b>HARDENER</b></div>
  </section>

  <section class="label label-small-front">
    <svg class="bands" viewBox="0 0 426 436" preserveAspectRatio="none" aria-hidden="true">
      <polygon points="0,180 426,320 426,436 0,436" fill="var(--green)"/>
      <polygon points="0,230 426,390 426,436 0,400" fill="var(--green-light)" opacity=".55"/>
      <polygon points="250,180 426,300 426,318 240,190" fill="var(--green-deep)"/>
    </svg>
    <div class="content">
      <p class="brand-name" style="left:24px; top:40px; font-size:48px;">VERANO<span>AUTOCOAT</span></p>
      <div style="position:absolute; left:24px; top:184px;">
        <span class="tag" style="font-size:23px;">ULTRA</span>
        <h2 class="product" style="font-size:26px; letter-spacing:1px; margin-top:4px; line-height:1.08;">HARDENER<br>FOR CLEAR COAT</h2>
        <div class="spec" style="font-size:21px; margin-top:4px;">VOC 2.1<br>2:1 MIX</div>
      </div>
      <div class="volume" style="left:82px; top:378px; font-size:30px;">2.5L</div>
      <div class="speed-badge" style="left:224px; top:367px;">SLOW</div>
    </div>
  </section>

</main>
</body>
</html>
```